Boutique custom software development company needs new business card

Our nearly 20 year old custom software development company would like to better include the fact that we are now providing Bitcoin services. These new services are B2B include education (how to acquire and securely hold Bitcoin) and integrating Bitcoin payments into existing ecommerce sites or other existing systems. Please keep the card clean and simple. Attached is our current design and some other files. vextorial.com

Target Market(s)

businesses owners interested in long term relationship

Industry/Entity Type

Custom software development and Bitcoin

Contact Information for Business Card

Dale Parker, dale@vextorial.com, vextorial.com, (888) 555-VXTRL

Font styles to use
Other font styles liked:
• monospace

Requirements
Must have
• double-sided
Nice to have
• clean and simple
Should not have
• physical address

```html
<!DOCTYPE html>
<html lang="en">
<head>
<meta charset="UTF-8">
<title>Vextorial — Business Card</title>
<link rel="stylesheet" href="https://fonts.googleapis.com/css2?family=Open+Sans:wght@400;600;700&family=Courier+Prime:wght@400;700&display=swap">
<style>
  :root {
    --brand-blue: #3470b8;
    --brand-blue-deep: #2f66aa;
    --brand-orange: #e0701e;
    --card-white: #f7f7f7;
    --text-grey: #4a4a4a;
    --stage: #e4e5e8;
  }
  * { box-sizing: border-box; margin: 0; padding: 0; }
  html, body {
    width: 1200px; height: 900px; overflow: hidden;
    background: var(--stage);
    font-family: "Open Sans", Arial, sans-serif;
  }
  .canvas { position: relative; width: 1200px; height: 900px; }
  .card {
    position: absolute; left: 300px;
    width: 600px; height: 343px;
    border-radius: 34px;
    box-shadow: 0 10px 28px rgba(0,0,0,0.18);
    overflow: hidden;
  }
  /* Front */
  .card-front {
    top: 84px;
    background: linear-gradient(100deg, var(--brand-blue-deep), var(--brand-blue));
    display: flex; flex-direction: column; align-items: center; justify-content: center;
    gap: 16px;
  }
  .front-mark { display: flex; align-items: center; gap: 14px; }
  .front-mark .mark-square {
    width: 22px; height: 22px; background: var(--brand-orange);
  }
  .front-mark .site {
    font-family: "Courier Prime", "Courier New", monospace;
    font-weight: 700; font-size: 30px; color: #ffffff;
    letter-spacing: 2px;
  }
  .front-services {
    font-family: "Courier Prime", "Courier New", monospace;
    font-weight: 400; font-size: 15px; color: #ffffff;
    letter-spacing: 1px; opacity: 0.9;
  }
  /* Back */
  .card-back {
    top: 473px;
    background: linear-gradient(120deg, #ececec, var(--card-white) 55%, #ffffff);
  }
  .brand { position: absolute; left: 28px; top: 52px; }
  .brand .wordmark {
    font-weight: 700; font-size: 58px; line-height: 1;
    color: var(--brand-blue); letter-spacing: -1px;
  }
  .brand .tagline {
    margin-top: 6px; margin-left: 40px;
    font-size: 19px; line-height: 1.3; color: var(--brand-blue); letter-spacing: -0.3px;
  }
  .brand .services {
    margin-top: 4px; margin-left: 40px;
    font-size: 14px; line-height: 1.3; color: var(--brand-orange); font-weight: 600;
  }
  .holder {
    position: absolute; right: 222px; top: 244px;
    font-weight: 600; font-size: 21px; color: var(--brand-blue);
    letter-spacing: -0.3px; text-transform: uppercase;
  }
  .divider {
    position: absolute; left: 392px; top: 198px;
    width: 1.5px; height: 84px; background: var(--brand-orange);
  }
  .contacts {
    position: absolute; left: 404px; top: 200px;
    list-style: none;
  }
  .contacts li {
    display: flex; align-items: center; gap: 7px;
    font-size: 14.5px; color: var(--text-grey); line-height: 27px;
  }
  .contacts svg { width: 15px; height: 15px; flex: none; }
</style>
</head>
<body>
<main class="canvas">
  <section class="card card-front" aria-label="Card front">
    <div class="front-mark">
      <span class="mark-square"></span>
      <span class="site">vextorial.com</span>
    </div>
    <div class="front-services">custom software &amp; Bitcoin services</div>
  </section>

  <section class="card card-back" aria-label="Card back">
    <div class="brand">
      <div class="wordmark">Vextorial</div>
      <div class="tagline">developer of custom applications</div>
      <div class="services">Bitcoin education &amp; payment integration</div>
    </div>

    <div class="holder">Dale Parker</div>
    <div class="divider"></div>

    <ul class="contacts">
      <li>
        <svg viewBox="0 0 16 16" aria-hidden="true"><path fill="#3470b8" d="M3.6 1.5l2.2 2.3-1.2 1.6c.9 2 2.1 3.2 4 4l1.6-1.2 2.3 2.2-1.5 2.3C6.5 12.4 3.6 9.5 1.3 3z"/></svg>
        (888) 555-VXTRL
      </li>
      <li>
        <svg viewBox="0 0 16 16" aria-hidden="true"><rect x="1.5" y="3.5" width="13" height="9" rx="1" fill="#3470b8"/><path d="M2 4.5l6 4.5 6-4.5" stroke="#fff" stroke-width="1.3" fill="none"/></svg>
        dale@vextorial.com
      </li>
      <li>
        <svg viewBox="0 0 16 16" aria-hidden="true"><circle cx="8" cy="8" r="6.2" fill="none" stroke="#3470b8" stroke-width="1.6"/><ellipse cx="8" cy="8" rx="2.6" ry="6.2" fill="none" stroke="#3470b8" stroke-width="1.2"/><path d="M2 8h12" stroke="#3470b8" stroke-width="1.2"/></svg>
        www.vextorial.com
      </li>
    </ul>
  </section>
</main>
</body>
</html>
```